Quorva - corporate Business Card

We need a good look and innovative business card for a new start up company based in Los Angeles called "Quorva". We are in a payment business, including payment card, app, and ewallet. We are expert in online payment and Card not present (CNP) transaction.
We need an innovative, modern business card.

Our logo font is Aero Matics

Target Market(s)

Startup - Bank - Online Payment - Card Manufacturing

Industry/Entity Type

Startup

Contact Information for Business Card

phone: 555 014 7396 - Address: 4172 Marlowe blvd, Brevan City, CA 90299

Requirements
Must have
• Message: innovative, professional, expert, high tech, trust, online payment expert, security
Nice to have
• no comment
Should not have
• no Comment

```html
<!DOCTYPE html>
<html lang="en">
<head>
<meta charset="utf-8">
<title>Quorva – Business Card</title>
<link rel="stylesheet" href="https://fonts.googleapis.com/css2?family=Open+Sans:wght@400;600;700&display=swap">
<style>
  :root {
    --brand-red: #b8202f;
    --backdrop: #222222;
    --paper: #ffffff;
    --blush: #f5e3de;
    --ink-grey: #8f8f8f;
    --rule-grey: #aaaaaa;
  }
  * { box-sizing: border-box; margin: 0; padding: 0; }
  html, body {
    width: 1189px;
    height: 1200px;
    overflow: hidden;
    background: var(--backdrop);
    font-family: "Open Sans", sans-serif;
  }
  .card {
    position: absolute;
    left: 171px;
    width: 855px;
    height: 487px;
    border-radius: 20px;
    overflow: hidden;
    box-shadow: 3px 5px 8px rgba(0,0,0,0.55);
  }
  .card-front { top: 68px; background: var(--brand-red); }
  .card-back { top: 626px; background: var(--paper); }

  .wordmark {
    position: absolute;
    display: flex;
    align-items: center;
  }
  .wordmark-dot { border-radius: 50%; flex: none; }
  .wordmark-name {
    font-family: "Open Sans", sans-serif;
    font-weight: 700;
    line-height: 1;
    letter-spacing: 1px;
  }
  .card-front .wordmark { left: 188px; top: 171px; gap: 18px; }
  .card-front .wordmark-dot { width: 146px; height: 146px; background: var(--paper); }
  .card-front .wordmark-name { font-size: 94px; color: var(--paper); margin-top: -14px; }

  .card-back .wordmark { left: 41px; top: 42px; gap: 14px; }
  .card-back .wordmark-dot { width: 120px; height: 120px; background: var(--brand-red); }
  .card-back .wordmark-name { font-size: 76px; color: var(--brand-red); margin-top: -12px; }

  .backdrop-disc {
    position: absolute;
    left: 512px;
    top: -79px;
    width: 424px;
    height: 424px;
    border-radius: 50%;
    background: var(--blush);
  }

  .holder { position: absolute; left: 43px; top: 297px; }
  .holder-name {
    font-weight: 700;
    font-size: 29px;
    line-height: 1;
    color: var(--brand-red);
  }
  .holder-title {
    font-weight: 400;
    font-size: 24px;
    line-height: 1;
    color: var(--ink-grey);
    margin-top: 2px;
  }
  .divider {
    position: absolute;
    left: 45px;
    top: 364px;
    width: 763px;
    height: 2px;
    background: var(--rule-grey);
  }
  .contact-list {
    position: absolute;
    left: 43px;
    top: 398px;
    list-style: none;
  }
  .contact-item {
    display: flex;
    align-items: center;
    gap: 10px;
    font-size: 23px;
    line-height: 29px;
    color: var(--ink-grey);
  }
  .contact-icon { width: 26px; height: 26px; flex: none; }
  .address {
    position: absolute;
    right: 37px;
    top: 400px;
    font-style: normal;
    text-align: right;
    font-size: 23px;
    line-height: 27px;
    color: var(--ink-grey);
  }
</style>
</head>
<body>

<section class="card card-front">
  <div class="wordmark">
    <span class="wordmark-dot"></span>
    <span class="wordmark-name">quorva</span>
  </div>
</section>

<section class="card card-back">
  <span class="backdrop-disc"></span>

  <div class="wordmark">
    <span class="wordmark-dot"></span>
    <span class="wordmark-name">quorva</span>
  </div>

  <div class="holder">
    <p class="holder-name">Dorian Vale</p>
    <p class="holder-title">Managing Director</p>
  </div>

  <span class="divider"></span>

  <ul class="contact-list">
    <li class="contact-item">
      <svg class="contact-icon" viewBox="0 0 26 26" aria-hidden="true">
        <circle cx="13" cy="13" r="13" fill="#b8202f"/>
        <path d="M6 11c0-3 3.5-4 7-4s7 1 7 4v1.5h-3.5v-2h-7v2H6z" fill="#fff"/>
        <rect x="8" y="13" width="10" height="6" rx="1" fill="#fff"/>
        <circle cx="13" cy="16" r="1.6" fill="#b8202f"/>
      </svg>
      <span>555 014 7396</span>
    </li>
    <li class="contact-item">
      <svg class="contact-icon" viewBox="0 0 26 26" aria-hidden="true">
        <circle cx="13" cy="13" r="13" fill="#b8202f"/>
        <rect x="6" y="8" width="14" height="10" fill="none" stroke="#fff" stroke-width="1.6"/>
        <path d="M6 8l7 6 7-6M6 18l5-5M20 18l-5-5" fill="none" stroke="#fff" stroke-width="1.6"/>
      </svg>
      <span>hello@quorvapay.com</span>
    </li>
  </ul>

  <address class="address">
    4172 Marlowe blvd,<br>
    Brevan City, CA 90299
  </address>
</section>

</body>
</html>
```